Card Design for my dog training business Brightpaw Obedience

Need a business card design for my dog training business with my new logo. Want the card to come off professional yet fun. Want it to be very eye catchy as well. I normally have these at vet clinics, pet stores, and groomers. so need it to look better than my competitors.
Target Market(s)
dog owners
Industry/Entity Type
Dog Training
Contact Information for Business Card
needs logo, my name and info
Font styles to use
Serif
Colors
0255a3
ffffff
ec1f27
000000
333333
fbfbfb
Requirements
Must have
- Brightpaw Obedience
- Felix Orland
- 415 903 2276
- info@brightpawobedience.example
- www.brightpawobedience.example

```html
<!DOCTYPE html>
<html lang="en">
<head>
<meta charset="utf-8">
<title>Brightpaw Obedience – Business Card</title>
<link href="https://fonts.googleapis.com/css2?family=EB+Garamond:ital,wght@0,500;1,400&family=Open+Sans:wght@400;700&display=swap" rel="stylesheet">
<style>
  :root {
    --backdrop: #3a332e;
    --card: #1b1b1d;
    --card-edge: #111112;
    --ink: #ffffff;
    --ink-soft: #e6e6e6;
    --emboss: #3a3a3d;
    --tagline: #8a8a8a;
  }
  * { margin: 0; padding: 0; box-sizing: border-box; }
  html, body { width: 1200px; height: 864px; overflow: hidden; }
  body {
    background: var(--backdrop);
    display: flex;
    flex-direction: column;
    align-items: center;
    justify-content: center;
    gap: 36px;
  }
  .card {
    position: relative;
    width: 680px;
    height: 389px;
    background: var(--card);
    border: 1px solid var(--card-edge);
    box-shadow: 0 10px 30px rgba(0,0,0,.45);
    overflow: hidden;
  }

  /* front */
  .card-front .emboss-mark {
    position: absolute;
    left: 0; right: 0; top: 120px;
    text-align: center;
    font-family: 'EB Garamond', serif;
    font-weight: 500;
    font-size: 44px;
    letter-spacing: 1px;
    color: var(--emboss);
  }
  .card-front .tagline {
    position: absolute;
    left: 0; right: 0; bottom: 90px;
    text-align: center;
    font-family: 'EB Garamond', serif;
    font-style: italic;
    font-size: 19px;
    color: var(--tagline);
  }

  /* back */
  .card-back .holder-name {
    position: absolute;
    left: 44px; top: 128px;
    font-family: 'Open Sans', sans-serif;
    font-weight: 700;
    font-size: 24px;
    color: var(--ink);
  }
  .card-back .rule {
    position: absolute;
    left: 44px; top: 172px;
    width: 592px; height: 1px;
    background: var(--ink-soft);
  }
  .card-back .contact-list {
    position: absolute;
    left: 44px; top: 186px;
    list-style: none;
    font-family: 'Open Sans', sans-serif;
    font-size: 16px;
    color: var(--ink);
    line-height: 26px;
  }
  .contact-list li { display: flex; align-items: center; gap: 10px; }
  .contact-list svg { width: 14px; height: 14px; fill: var(--ink); flex: none; }
  .card-back .brand-mark {
    position: absolute;
    right: 40px; top: 70px;
    width: 150px;
    text-align: center;
    font-family: 'EB Garamond', serif;
    font-weight: 500;
    font-size: 26px;
    line-height: 1.1;
    color: var(--ink);
  }
</style>
</head>
<body>
  <section class="card card-front">
    <div class="emboss-mark">Brightpaw Obedience</div>
    <p class="tagline">“Teaching good manners one happy dog at a time.”</p>
  </section>

  <section class="card card-back">
    <h1 class="holder-name">Felix Orland</h1>
    <div class="rule"></div>
    <ul class="contact-list">
      <li>
        <svg viewBox="0 0 16 16" aria-hidden="true"><path d="M3 1h3l1 4-2 1.5a9 9 0 0 0 4.5 4.5L11 9l4 1v3a2 2 0 0 1-2 2A13 13 0 0 1 1 3a2 2 0 0 1 2-2z"/></svg>
        415 903 2276
      </li>
      <li>
        <svg viewBox="0 0 16 16" aria-hidden="true"><path d="M1 3h14v10H1z M1 3l7 6 7-6" fill="none" stroke="#fff" stroke-width="1.6"/></svg>
        info@brightpawobedience.example
      </li>
      <li>
        <svg viewBox="0 0 16 16" aria-hidden="true"><circle cx="8" cy="8" r="7"/></svg>
        www.brightpawobedience.example
      </li>
    </ul>
    <div class="brand-mark">Brightpaw Obedience</div>
  </section>
</body>
</html>
```